MV Decor

There is a sample provided with the arabic text of the business card. please copy paste the same text and the same Logo (The two triangles) Just try to incorproate the Brown background attached (you are free to change the colors) Id like the colors to be mainly shades of black and red.

```html
<!DOCTYPE html>
<html lang="ar">
<head>
<meta charset="utf-8">
<title>MV Decor – Business Card</title>
<link rel="stylesheet" href="https://fonts.googleapis.com/css2?family=Aref+Ruqaa:wght@700&family=Reem+Kufi:wght@500;700&family=Roboto:wght@500&display=swap">
<style>
  :root{
    --red:#d8223f;
    --charcoal:#2a292b;
    --charcoal-dark:#1f1e20;
    --pattern:#3a393c;
    --white:#ffffff;
    --stage:#d9d9d9;
  }
  *{box-sizing:border-box;margin:0;padding:0}
  html,body{width:1200px;height:873px;overflow:hidden;background:var(--stage)}
  .canvas{position:relative;width:1200px;height:873px}
  .card{position:absolute;top:262px;width:540px;height:348px;background:var(--charcoal);overflow:hidden;box-shadow:0 6px 18px rgba(0,0,0,.25)}
  .card--front{left:40px}
  .card--back{left:620px}
  .card svg.shapes{position:absolute;inset:0}

  .brand-name{position:absolute;left:10px;top:160px;width:150px;display:flex;align-items:center;justify-content:center;gap:6px;
    font-family:"Reem Kufi",sans-serif;font-weight:700;font-size:19px;color:var(--white);letter-spacing:.5px}
  .brand-name .brand-square{width:9px;height:9px;background:var(--white)}

  .front-info{position:absolute;right:22px;top:22px;width:310px;direction:rtl;text-align:right;color:var(--white)}
  .person-name{font-family:"Aref Ruqaa",serif;font-weight:700;font-size:27px;line-height:1.2}
  .person-title{font-family:"Aref Ruqaa",serif;font-weight:700;font-size:17px;margin:2px 40px 14px 0}
  .qual-block{display:flex;gap:10px}
  .qual-block .divider{width:1px;background:var(--white);margin-top:4px}
  .qualifications{list-style:none;font-family:"Reem Kufi",sans-serif;font-weight:500;font-size:17px;line-height:1.45}
  .phone{display:flex;align-items:center;gap:8px;margin-top:12px;font-family:"Roboto",sans-serif;font-weight:500;font-size:18px;direction:ltr;justify-content:flex-end}

  .back-info{position:absolute;right:24px;top:62px;direction:rtl;text-align:right;color:var(--white);list-style:none;
    font-family:"Reem Kufi",sans-serif;font-weight:500;font-size:17px;line-height:1.55}
  .back-info li{display:flex;align-items:center;gap:10px}
  .back-info li::before{content:"";width:9px;height:9px;background:var(--red);outline:2px solid var(--white);flex:none}
</style>
</head>
<body>
<main class="canvas">

  <section class="card card--front" aria-label="Business card front">
    <svg class="shapes" width="540" height="348" viewBox="0 0 540 348">
      <rect x="0" y="0" width="260" height="348" fill="var(--pattern)" role="img" aria-label="Subtle checker and circle pattern"/>
      <polygon points="230,0 540,0 540,348 230,348 160,174" fill="var(--red)"/>
      <polyline points="236,6 166,174 236,342" fill="none" stroke="var(--white)" stroke-width="1.5"/>
      <polygon points="85,84 175,174 85,264 -5,174" fill="var(--red)"/>
      <polygon points="85,96 163,174 85,252 7,174" fill="none" stroke="var(--white)" stroke-width="3"/>
    </svg>
    <div class="brand-name"><span class="brand-square"></span>MV Decor</div>

    <div class="front-info">
      <p class="person-name">المهندس / سامي ناصر الفارس</p>
      <p class="person-title">أستاذ جامعي</p>
      <div class="qual-block">
        <ul class="qualifications">
          <li>ماجستير هندسة ديكور</li>
          <li>دبلوم عالي فن تشكيلي (المدينة)</li>
          <li>أكاديمية النخيل هندسة - فنية</li>
          <li>استشارات هندسية - فنية</li>
        </ul>
        <span class="divider"></span>
      </div>
      <p class="phone">35550142 / 66500318
        <svg width="16" height="16" viewBox="0 0 24 24" aria-hidden="true"><path fill="var(--white)" d="M6.6 10.8a15 15 0 0 0 6.6 6.6l2.2-2.2c.3-.3.7-.4 1-.2 1.1.4 2.3.6 3.6.6.6 0 1 .4 1 1V20c0 .6-.4 1-1 1A17 17 0 0 1 3 4c0-.6.4-1 1-1h3.5c.6 0 1 .4 1 1 0 1.3.2 2.5.6 3.6.1.3 0 .7-.2 1z"/></svg>
      </p>
    </div>
  </section>

  <section class="card card--back" aria-label="Business card back">
    <svg class="shapes" width="540" height="348" viewBox="0 0 540 348">
      <rect x="220" y="0" width="320" height="348" fill="var(--pattern)" role="img" aria-label="Subtle checker and circle pattern"/>
      <rect x="0" y="0" width="190" height="348" fill="var(--charcoal-dark)"/>
      <polygon points="95,60 180,174 95,288 10,174" fill="var(--red)"/>
      <polygon points="95,76 168,174 95,272 22,174" fill="none" stroke="var(--charcoal-dark)" stroke-width="3"/>
      <rect x="190" y="0" width="34" height="348" fill="var(--red)"/>
      <line x1="186" y1="0" x2="186" y2="348" stroke="var(--white)" stroke-width="3"/>
      <line x1="228" y1="0" x2="228" y2="348" stroke="var(--white)" stroke-width="3"/>
    </svg>
    <ul class="back-info">
      <li>ماجستير هندسة ديكور</li>
      <li>دبلوم عالي فن تشكيلي (المدينة)</li>
      <li>أكاديمية النخيل هندسة - فنية</li>
      <li>استشارات هندسية - فنية</li>
      <li>ماجستير هندسة ديكور</li>
      <li>دبلوم عالي فن تشكيلي (المدينة)</li>
      <li>أكاديمية النخيل هندسة - فنية</li>
      <li>استشارات هندسية - فنية</li>
    </ul>
  </section>

</main>
</body>
</html>
```